Meadow Paw Web Site

We have basically a start up business that I need help with. This project is just for the web site.

Our product is a frozen raw pet food that promotes weight control, less shedding, smaller stools and an overall better health. The product is in nugget form similar to what you would see in a steak shish kabob. I only share that with you in case you want to incorporate that in the design.

We have been in business for 17 years but all of our sales have been word of mouth. We are going to be launching an infomercial this summer and I need everything stated previously to be completed before we can launch the infomercial.

We need the following (6) pages:

Home:
This is where we need to have the ability to purchase our products. Our main goal is to get the consumer to purchase our product. We have our own shopping cart so we just need to allow for the insertion of that shopping cart.

Why Raw:
This will just be a page with 4-5 paragraphs and an embedded YouTube video.

How to Use:
We will need a page with a chart (4 Columns wide with 6 rows) as well as an embedded YouTube video.

Customer Success Stories:
Allow us to add these as we move forward. I need a placeholder for an image of the customers pet and a paragraph or two explaining the situation

Where to Buy:
- Online - Find a Retailer - Find a Local Distributor - Call to Order

Contact Us:
Copper Ridge Holdings, Inc.
2740 Copper Rd
Eagan, MN 55148
(800) xxx-xxxx

We need to provide links to our to be created... Facebook page, Twitter Account, Youtube Channel, Google circle, Blog
Updates

All, I have received many front page designs that look good.  Please notice in the brief that I need multiple pages built not just the home page.  

Thanks,

Dale

Reason: I need to see the rest of the pages. Thanks, Dale

Target Market(s)

Women between the ages of 30 & 60.

Industry/Entity Type

Shopping

```html
<!DOCTYPE html>
<html lang="en">
<head>
<meta charset="utf-8">
<title>Meadow Paw — Where Raw</title>
<link href="https://fonts.googleapis.com/css2?family=Oswald:wght@400&family=Ubuntu:wght@400;500&display=swap" rel="stylesheet">
<style>
:root{
  --orange:#d4530f;
  --orange-light:#ee7a1c;
  --orange-dark:#b8420a;
  --title:#c5480e;
  --ink:#2a2a2a;
  --dark-ink:#3a2a10;
  --bg:#f6eeee;
  --card:#ffffff;
  --footer:#2b2b2b;
  --footer-bottom:#1f1f1f;
  --footer-text:#9a9a9a;
  --footer-head:#f0f0f0;
  --yellow:#f7d21a;
}
*{box-sizing:border-box;margin:0;padding:0}
html,body{width:813px;height:1200px;overflow:hidden}
body{font-family:"Ubuntu",sans-serif;background:var(--bg);position:relative;color:var(--ink)}
.header{position:absolute;left:0;top:0;width:813px;height:132px;background:linear-gradient(180deg,#d9d7d5 0%,#efecea 100%)}
.brand{position:absolute;left:82px;top:44px;display:flex;align-items:center;gap:8px}
.brand-mark{width:26px;height:26px;background:var(--orange)}
.brand-name{font-family:"Oswald",sans-serif;font-size:26px;color:var(--orange);line-height:1}
.account-links{position:absolute;right:82px;top:16px;font-size:8px;font-weight:500;color:var(--title);letter-spacing:.1px}
.account-links span{margin:0 3px;color:#555}
.btn{position:absolute;top:44px;height:16px;border-radius:8px;font-size:8.5px;display:flex;align-items:center;justify-content:center}
.btn-signin{left:613px;width:56px;background:linear-gradient(#ee7a1c,#c9480c);color:#fff}
.btn-register{left:675px;width:56px;background:linear-gradient(#fbe04a,#eebc0f);color:#3a2a00}
.cart{position:absolute;left:421px;top:80px;display:flex;align-items:center;gap:6px;font-family:"Oswald",sans-serif;font-size:10px;color:var(--orange-dark)}
.cart .items{margin-left:18px}
.search{position:absolute;left:586px;top:79px;width:145px;height:22px;border-radius:11px;background:#fff;border:1px solid #d8d2cc;display:flex;align-items:center;justify-content:space-between;padding:0 8px 0 12px;font-size:8.5px;color:#777}
.nav{position:absolute;left:82px;top:117px;width:649px;height:31px;border-radius:4px;background:linear-gradient(#ee7a1c,#cf4f0c);display:grid;grid-template-columns:52px 98px 117px 129px 145px 108px;box-shadow:0 1px 0 #a33c08}
.nav a{display:flex;align-items:center;justify-content:center;color:#fff;text-decoration:none;font-family:"Oswald",sans-serif;font-size:13px;border-right:1px solid #b8450a;box-shadow:1px 0 0 #f18a3a}
.nav a:last-child{border-right:none;box-shadow:none}
.page-title{position:absolute;left:82px;top:170px;width:649px;height:26px;border-bottom:1px dashed #b9b0a8;font-family:"Oswald",sans-serif;font-size:19px;color:var(--dark-ink);line-height:24px}
.page-title em{font-style:normal;color:var(--title)}
.story{position:absolute;left:82px;width:649px;height:171px;background:var(--card);border-bottom:2px solid #dcd6d0}
.story-media{position:absolute;left:3px;top:3px;width:284px;height:163px;display:flex;align-items:center;justify-content:center}
.story-body{position:absolute;left:312px;top:13px;width:316px}
.story-title{font-family:"Oswald",sans-serif;font-size:15.5px;color:var(--title);font-weight:400;margin-bottom:7px}
.story-text{font-size:8.3px;line-height:13px;color:var(--ink)}
.footer{position:absolute;left:0;top:984px;width:813px;height:186px;background:var(--footer)}
.footer-col{position:absolute;top:22px;height:145px;border-right:1px dashed #4a4a4a}
.footer-col h3{font-family:"Oswald",sans-serif;font-weight:400;font-size:14px;color:var(--footer-head);margin-bottom:9px}
.footer-col li{list-style:none;font-size:8.3px;color:var(--footer-text);line-height:16.3px}
.contact-sub{font-size:8.5px;color:var(--footer-text);line-height:14px}
.contact-note{font-size:7px;color:var(--footer-text);line-height:13px}
.contact-phone{display:flex;align-items:center;gap:5px;font-size:8.5px;color:var(--footer-text);margin-top:6px}
.newsletter{position:absolute;left:570px;top:22px;width:161px}
.newsletter h3{font-family:"Oswald",sans-serif;font-weight:400;font-size:14px;color:var(--footer-head);margin-bottom:9px}
.newsletter p{font-size:8.3px;color:var(--footer-text);line-height:11px}
.email{margin-top:9px;height:21px;background:#fff;border:1px solid #ccc;font-size:9px;color:#aaa;padding:4px 6px}
.subscribe{margin:7px 0 0 auto;width:58px;height:19px;background:var(--orange-dark);color:#fff;font-size:9.5px;display:flex;align-items:center;justify-content:center}
.social{display:flex;justify-content:flex-end;gap:6px;margin-top:11px}
.social span{width:18px;height:18px;border-radius:2px}
.bottom-bar{position:absolute;left:0;top:1170px;width:813px;height:30px;background:var(--footer-bottom);font-size:7.8px;color:#6f6f6f;padding:12px 82px}
</style>
</head>
<body>
<header class="header">
  <div class="brand"><span class="brand-mark"></span><span class="brand-name">Meadow Paw</span></div>
  <div class="account-links">MY ACCOUNT<span>/</span>WISH LIST<span>/</span>MY CART<span>/</span>CHECKOUT</div>
  <div class="btn btn-signin">Sing in</div>
  <div class="btn btn-register">Register</div>
  <div class="cart">
    <svg width="18" height="15" viewBox="0 0 18 15" aria-hidden="true"><path d="M1 5h16l-2 9H3z" fill="none" stroke="#c5480e" stroke-width="1.6"/><path d="M5 5l4-4 4 4" fill="none" stroke="#c5480e" stroke-width="1.6"/><path d="M6 8v3M9 8v3M12 8v3" stroke="#c5480e" stroke-width="1.3"/></svg>
    <span>SHOPPING CART</span><span class="items">(2) ITEMS</span>
  </div>
  <div class="search"><span>Search.......</span>
    <svg width="11" height="11" viewBox="0 0 11 11" aria-hidden="true"><circle cx="4.5" cy="4.5" r="3.3" fill="none" stroke="#c5480e" stroke-width="1.8"/><path d="M7 7l3 3" stroke="#c5480e" stroke-width="2"/></svg>
  </div>
  <nav class="nav">
    <a href="#" aria-label="Home"><svg width="15" height="13" viewBox="0 0 15 13"><path d="M7.5 0L0 6.5h2V13h4V9h3v4h4V6.5h2z" fill="#fff"/></svg></a>
    <a href="#">Why Raw</a><a href="#">How to Use</a><a href="#">Where to Buy</a><a href="#">Success Stories</a><a href="#">Contact Us</a>
  </nav>
</header>

<h1 class="page-title" style="font-weight:400">WHERE <em>RAW</em></h1>

<article class="story" style="top:219px">
  <div class="story-media" role="img" aria-label="Video still: a puppy and a bulldog playing on grass" style="background:linear-gradient(160deg,#8a9a48 0%,#d9cbb0 45%,#6f8a34 100%)">
    <svg width="42" height="42" viewBox="0 0 42 42" aria-hidden="true"><circle cx="21" cy="21" r="19" fill="rgba(40,40,40,.55)" stroke="#eee" stroke-width="2"/><path d="M16 12l13 9-13 9z" fill="#eee"/></svg>
  </div>
  <div class="story-body"><h2 class="story-title">Nulla ullamcorper lacus eget purus</h2>
  <p class="story-text">Lorem ipsum dolor sit amet, consectetur adipiscing elit. Nulla ornare, nisi ut interdum condimentum, felis lectus pharetra nunc, nec tristique quam mi eu nunc. Nulla ornare sagittis ante, id sollicitudin nunc. Vestibulum ut sodales nisi. Pellentesque nunc dolor, faucibus in erat a, hendrerit mattis elit. Duis ornare mi ut risus egestas malesuada.</p></div>
</article>

<article class="story" style="top:409px">
  <div class="story-media" role="img" aria-label="Video still: a baby sitting on grass beside puppies eating from bowls" style="background:linear-gradient(170deg,#3f6e2a 0%,#5d8b3a 50%,#4a6f30 100%)">
    <svg width="42" height="42" viewBox="0 0 42 42" aria-hidden="true"><circle cx="21" cy="21" r="19" fill="rgba(40,40,40,.55)" stroke="#eee" stroke-width="2"/><path d="M16 12l13 9-13 9z" fill="#eee"/></svg>
  </div>
  <div class="story-body"><h2 class="story-title">Lorem ipsum dolor sit amet</h2>
  <p class="story-text">Aenean turpis lorem, volutpat id facilisis in, volutpat a metus. Fusce eget ante lacinia, porttitor mauris nec, euismod mi. Nullam eros turpis, congue non mollis malesuada, scelerisque non elit. Integer sit amet elementum ante. Suspendisse semper, erat a accumsan fringilla, risus ligula fermentum ligula, ac rhoncus arcu libero non nunc. Cras varius, mauris malesuada mattis pulvinar, leo nunc pretium sapien, eu ultricies mauris diam eget nulla.</p></div>
</article>

<article class="story" style="top:599px">
  <div class="story-media" role="img" aria-label="Video still: a puppy playing with a football on grass" style="background:linear-gradient(150deg,#4d8a2c 0%,#b98a52 45%,#4f8d30 100%)">
    <svg width="42" height="42" viewBox="0 0 42 42" aria-hidden="true"><circle cx="21" cy="21" r="19" fill="rgba(40,40,40,.55)" stroke="#eee" stroke-width="2"/><path d="M16 12l13 9-13 9z" fill="#eee"/></svg>
  </div>
  <div class="story-body"><h2 class="story-title">Suspendisse faucibus est ornare</h2>
  <p class="story-text">Duis et diam nunc. Aliquam vitae augue volutpat, ornare turpis condimentum, cursus dolor. Cras mattis faucibus eros quis convallis. Vestibulum laoreet ac ipsum sit amet venenatis. Nam ac velit iaculis, semper nunc sit amet, suscipit tortor. In rutrum lorem urna, lacinia laoreet tellus commodo sit amet. Curabitur posuere mattis dui, ut consectetur mi tempus eu.</p></div>
</article>

<article class="story" style="top:789px">
  <div class="story-media" role="img" aria-label="Video still: a dog eating nuggets from a steel bowl" style="background:linear-gradient(170deg,#c9b49a 0%,#8a5a34 50%,#a9a39a 100%)">
    <svg width="42" height="42" viewBox="0 0 42 42" aria-hidden="true"><circle cx="21" cy="21" r="19" fill="rgba(40,40,40,.55)" stroke="#eee" stroke-width="2"/><path d="M16 12l13 9-13 9z" fill="#eee"/></svg>
  </div>
  <div class="story-body"><h2 class="story-title">Proin nec tortor eget</h2>
  <p class="story-text">There are many variations of passages of Lorem Ipsum available, but the majority have suffered alteration in some form, by injected humour, or randomised words which don't look even slightly believable. If you are going to use a passage of Lorem Ipsum, you need to be sure there isn't anything embarrassing hidden in the middle of text.</p></div>
</article>

<footer class="footer">
  <div class="footer-col" style="left:82px;width:84px"><h3>Quick Links</h3><ul><li>Why Raw</li><li>How to Use</li><li>Where to Buy</li><li>Success Stories</li><li>How to Use</li><li>Where to Buy</li><li>Contact Us</li></ul></div>
  <div class="footer-col" style="left:185px;width:87px"><h3>Top Products</h3><ul><li>Product 1</li><li>Product 2</li><li>Product 3</li><li>Product 4</li><li>Product 5</li><li>Product 6</li><li>Product 7</li></ul></div>
  <div class="footer-col" style="left:290px;width:106px"><h3>Where to Buy</h3><ul><li>Find a Retailer</li><li>Find a Local Distributor</li><li>Call to Order</li></ul></div>
  <div class="footer-col" style="left:417px;width:136px"><h3>Contact Information</h3>
    <p class="contact-sub">PUBLISHING PACKAGES</p>
    <p class="contact-note">Lorem Ipsum is therefore always free<br>from repetition</p>
    <p class="contact-phone"><svg width="12" height="13" viewBox="0 0 12 13" aria-hidden="true"><path d="M2 1l3 2-1 2.5c1 2 2 3 3.5 4L10 8.5l2 3-2 1.5C5 12 1 7 0 2.5z" fill="#bbb"/></svg>+0 (000) 000-0000</p>
  </div>
  <div class="newsletter"><h3>Newsletter</h3>
    <p>combined with a handful of model sentence structures.</p>
    <div class="email">Email address</div>
    <div class="subscribe">Subscribe</div>
    <div class="social" aria-label="Social links">
      <span style="background:#3b6cc4"></span><span style="background:#3e5a72"></span><span style="background:#f29a12"></span><span style="background:#d23c2a"></span><span style="background:#b92c22"></span>
    </div>
  </div>
</footer>
<div class="bottom-bar">Company Name © 2014. Privacy Policy</div>
</body>
</html>
```